Business card design needed

I would like a one sided black business card with the information provided above. Refer to my website www.brightvolleyracquets.com.au for an example of colors I have used for my site, would like to keep this consistent for my business cards also, I will upload my logo below.

I am a new small business that provides tennis customers with racquet re stringing, tennis strings and accessories.

Industry/Entity Type

Small Business

Contact Information for Business Card

Bright Volley Tennis

Owen Whitby
Managing Director

brightvolleyracquets@mailbox.example
www.brightvolleyracquets.com.au
0491 726 305

Racquet Restringing/Tennis Strings/Accessories

Requirements
Must have
• Must have my logo and card must be black

```html
<!DOCTYPE html>
<html lang="en">
<head>
<meta charset="utf-8">
<title>Bright Volley Tennis – Business Card</title>
<link rel="stylesheet" href="https://fonts.googleapis.com/css2?family=Open+Sans:wght@400;700&display=swap">
<style>
  :root {
    --stage: #e4e1dc;
    --card: #050505;
    --lime: #bfd843;
    --blue: #2b5e91;
    --white: #ffffff;
  }
  html, body {
    margin: 0;
    width: 1200px;
    height: 750px;
    overflow: hidden;
    background: var(--stage);
    font-family: "Open Sans", Arial, sans-serif;
  }
  .business-card {
    position: absolute;
    left: 75px;
    top: 75px;
    width: 1050px;
    height: 598px;
    background: var(--card);
    border-radius: 40px;
    overflow: hidden;
    color: var(--white);
  }
  .band {
    position: absolute;
    top: 120px;
    height: 78px;
  }
  .band--blue { left: 0; width: 103px; background: var(--blue); }
  .band--lime { right: 0; width: 317px; background: var(--lime); }
  .brand-name {
    position: absolute;
    left: 113px;
    width: 610px;
    top: 126px;
    margin: 0;
    text-align: center;
    font-size: 46px;
    line-height: 66px;
    font-weight: 700;
    color: var(--lime);
    letter-spacing: 0.5px;
  }
  .contact {
    position: absolute;
    left: 112px;
    top: 345px;
  }
  .contact__name {
    margin: 0;
    font-size: 31px;
    font-weight: 700;
    line-height: 44px;
    color: var(--lime);
  }
  .contact__role {
    margin: 0 0 8px;
    font-size: 24px;
    line-height: 34px;
  }
  .contact__list {
    list-style: none;
    margin: 0;
    padding: 0;
  }
  .contact__item {
    display: flex;
    align-items: center;
    height: 44px;
    font-size: 24px;
  }
  .contact__icon {
    width: 24px;
    height: 20px;
    margin-right: 16px;
    fill: var(--lime);
    flex: none;
  }
  .services {
    position: absolute;
    right: 47px;
    top: 425px;
    list-style: none;
    margin: 0;
    padding: 0;
    text-align: right;
  }
  .services__item {
    font-size: 31px;
    line-height: 45px;
  }
  .services__item::before {
    content: "";
    display: inline-block;
    width: 10px;
    height: 10px;
    margin-right: 12px;
    vertical-align: 7px;
    background: var(--white);
  }
</style>
</head>
<body>
  <article class="business-card">
    <div class="band band--blue"></div>
    <div class="band band--lime"></div>
    <h1 class="brand-name">Bright Volley Tennis</h1>

    <section class="contact">
      <p class="contact__name">Owen Whitby</p>
      <p class="contact__role">Managing Director</p>
      <ul class="contact__list">
        <li class="contact__item">
          <svg class="contact__icon" viewBox="0 0 24 20" aria-hidden="true">
            <path d="M1 6 Q12 -1 23 6 L20 9 L16 7 L16 5 Q12 4 8 5 L8 7 L4 9 Z"/>
            <path d="M6 9 L18 9 L21 18 L3 18 Z"/>
          </svg>
          0491 726 305
        </li>
        <li class="contact__item">
          <svg class="contact__icon" viewBox="0 0 24 20" aria-hidden="true">
            <path d="M2 5 L21 2 L23 15 L4 18 Z M5 7 L13 11 L19 5 L19.5 6 L13 13 L5 9 Z" fill-rule="evenodd"/>
          </svg>
          brightvolleyracquets@mailbox.example
        </li>
        <li class="contact__item">
          <svg class="contact__icon" viewBox="0 0 24 20" aria-hidden="true">
            <circle cx="12" cy="10" r="9"/>
            <path d="M3 10 H21 M12 1 V19 M12 1 Q6 10 12 19 M12 1 Q18 10 12 19" stroke="#050505" stroke-width="1.2" fill="none"/>
          </svg>
          www.brightvolleyracquets.com.au
        </li>
      </ul>
    </section>

    <ul class="services">
      <li class="services__item">Racquet Restringing</li>
      <li class="services__item">Tennis Strings</li>
      <li class="services__item">Accessories</li>
    </ul>
  </article>
</body>
</html>
```